Marlowe Group needs a business card

I would like the card to be simple but modern and elegant.
I like black and white.
or black and gold.
we are a private finance lender and also are involved in property and property developments.

please look at the business card photos i provided i would like M.G only one one side and all the other details on the other side use fonts that tie in with my theme.

Industry/Entity Type

Finance

Contact Information for Business Card

Marlowe Group (M.G) Daniel Marlowe M: 0413586207 E: danmarl@inboxmail.test

Font styles to use
Other font styles liked:
• Use fonts that would reflect our business

Colors
000000
ffffff

Requirements
Must have
• one side of details
• other side has either M.G or Marlowe Group like in the photos provided

```html
<!DOCTYPE html>
<html lang="en">
<head>
<meta charset="utf-8">
<title>Marlowe Group — Business Card</title>
<link rel="stylesheet" href="https://fonts.googleapis.com/css2?family=Cinzel:wght@400;700&family=Lato:wght@400&display=swap">
<style>
  :root {
    --backdrop: #6d6d6d;
    --card: #000000;
    --gold: #f2c12e;
    --gold-light: #fbe6a6;
    --gold-deep: #f7c531;
    --white: #ffffff;
  }
  * { margin: 0; padding: 0; box-sizing: border-box; }
  html, body { width: 1200px; height: 900px; overflow: hidden; }
  body { background: var(--backdrop); position: relative; }

  .card {
    position: absolute;
    top: 271px;
    width: 457px;
    height: 282px;
    background: var(--card);
    border-radius: 14px;
    overflow: hidden;
    box-shadow: 2px 3px 6px rgba(0,0,0,0.35);
  }
  .card--details { left: 137px; }
  .card--brand { left: 626px; width: 458px; }

  .holder-name {
    position: absolute;
    left: 32px;
    top: 41px;
    font-family: "Cinzel", serif;
    font-weight: 700;
    font-size: 16px;
    letter-spacing: 0.3px;
    color: var(--gold);
  }

  .contact-list {
    position: absolute;
    left: 32px;
    top: 198px;
    list-style: none;
    font-family: "Lato", sans-serif;
    font-size: 13px;
    color: var(--white);
  }
  .contact-list li { display: flex; align-items: center; height: 19px; }
  .contact-list svg { width: 10px; height: 10px; margin-right: 7px; flex: none; }

  .brand-mark {
    position: absolute;
    right: 26px;
    top: 74px;
    display: flex;
    flex-direction: column;
    align-items: center;
  }
  .brand-square {
    width: 64px;
    height: 64px;
    border: 3px solid var(--gold);
    margin-bottom: 30px;
  }
  .brand-name {
    font-family: "Cinzel", serif;
    font-weight: 400;
    font-size: 19px;
    color: var(--gold);
    white-space: nowrap;
  }

  .band {
    position: absolute;
    left: 0;
    width: 100%;
    height: 14px;
    background: linear-gradient(90deg, var(--gold-deep) 0%, var(--gold-deep) 45%, var(--gold-light) 62%, var(--gold-deep) 80%, var(--gold-deep) 100%);
  }
  .band--top { top: 0; }
  .band--bottom { bottom: 0; }

  .brand-initials {
    position: absolute;
    left: 0;
    right: 0;
    top: 100px;
    text-align: center;
    font-family: "Cinzel", serif;
    font-weight: 400;
    font-size: 72px;
    line-height: 80px;
    color: var(--gold);
  }
</style>
</head>
<body>
  <section class="card card--details">
    <h1 class="holder-name">DANIEL MARLOWE</h1>
    <ul class="contact-list">
      <li>
        <svg viewBox="0 0 10 10" aria-hidden="true"><rect x="2.5" y="0.5" width="5" height="9" rx="1" fill="none" stroke="#f2c12e" stroke-width="1.2"/></svg>
        0413586207
      </li>
      <li>
        <svg viewBox="0 0 10 10" aria-hidden="true"><rect x="0.5" y="2" width="9" height="6" fill="#f2c12e"/><path d="M0.5 2 L5 5.5 L9.5 2" fill="none" stroke="#000" stroke-width="0.9"/></svg>
        danmarl@inboxmail.test
      </li>
    </ul>
    <div class="brand-mark">
      <div class="brand-square"></div>
      <p class="brand-name">Marlowe Group</p>
    </div>
  </section>

  <section class="card card--brand">
    <div class="band band--top"></div>
    <p class="brand-initials">M.G</p>
    <div class="band band--bottom"></div>
  </section>
</body>
</html>
```